Stationary design for new digital markerting company

I need a stationary design for a new digital marketing company called Mossy Lantern.
We work with businesses to help them create and increase their online presence in order to increase awareness of their brand.
The design must keep with the colour schemes of our logo.
I would like a design that stands out but isn't over the top while also being professional and sophisticated.

Target Market(s)

other businesses

Industry/Entity Type

Business Consultant

Font styles to use
Sans Serif

Colors
abd036
ffffff
a54499

Requirements
Must have
• logo, plus the same colour scheme

```html
<!DOCTYPE html>
<html lang="en">
<head>
<meta charset="utf-8">
<title>Mossy Lantern — Business Card</title>
<link rel="stylesheet" href="https://fonts.googleapis.com/css2?family=Mulish:wght@400;700&display=swap">
<style>
  :root {
    --backdrop: #1d1d1f;
    --paper: #f7f7f5;
    --plum: #9b1e75;
    --plum-soft: #a8327f;
    --leaf: #67a61d;
    --ink: #333333;
    --white: #ffffff;
  }
  * { box-sizing: border-box; margin: 0; padding: 0; }
  html, body {
    width: 1200px; height: 1000px; overflow: hidden;
    background: var(--backdrop);
    font-family: "Mulish", Arial, sans-serif;
  }
  .canvas { position: relative; width: 1200px; height: 1000px; }

  .card {
    position: absolute;
    width: 580px; height: 323px;
    overflow: hidden;
  }

  /* Front */
  .card-front { left: 200px; top: 150px; background: var(--paper); }
  .front-top { position: absolute; left: 0; top: 0; width: 100%; height: 163px; }
  .front-band {
    position: absolute; left: 0; top: 163px; width: 100%; height: 124px;
    background: var(--plum);
  }
  .front-band .notch {
    position: absolute; left: 376px; top: 0;
    width: 0; height: 0;
    border-left: 10px solid transparent;
    border-right: 10px solid transparent;
    border-top: 16px solid var(--paper);
  }
  .front-stripe {
    position: absolute; left: 0; top: 287px; width: 100%; height: 36px;
    background: var(--leaf);
  }

  .brand { position: absolute; display: flex; align-items: center; }
  .brand-dot { border-radius: 50%; background: var(--leaf); flex: none; }
  .brand-text { display: flex; flex-direction: column; }
  .brand-name {
    font-weight: 400; text-transform: uppercase; letter-spacing: 1px; line-height: 1;
  }
  .brand-tagline { font-weight: 700; letter-spacing: 2px; line-height: 1; }

  .card-front .brand { left: 31px; top: 71px; }
  .card-front .brand-dot { width: 42px; height: 42px; margin-right: 24px; }
  .card-front .brand-name { font-size: 25px; color: var(--plum); }
  .card-front .brand-tagline { font-size: 9.5px; color: var(--ink); margin-top: 5px; }

  .person { position: absolute; left: 381px; top: 68px; }
  .person-name {
    font-size: 18px; font-weight: 700; color: var(--leaf);
    letter-spacing: 0.5px; text-transform: uppercase; line-height: 1.2;
  }
  .person-title { font-size: 15px; color: var(--ink); line-height: 1.3; }

  .address {
    position: absolute; left: 32px; top: 35px;
    font-size: 14px; line-height: 18px; color: var(--white); font-style: normal;
  }
  .contacts {
    position: absolute; left: 378px; top: 35px; list-style: none;
    font-size: 14px; line-height: 18px; color: var(--white);
  }
  .contacts li { display: flex; align-items: center; gap: 8px; }
  .contacts svg { width: 14px; height: 14px; flex: none; }

  /* Back */
  .card-back { left: 420px; top: 548px; background: var(--plum); }
  .card-back .brand { left: 112px; top: 138px; }
  .card-back .brand-dot { width: 48px; height: 48px; margin-right: 30px; }
  .card-back .brand-name { font-size: 29px; color: var(--white); }
  .card-back .brand-tagline { font-size: 11px; color: var(--white); margin-top: 6px; letter-spacing: 2.6px; }
</style>
</head>
<body>
<main class="canvas">

  <section class="card card-front" aria-label="Business card front">
    <div class="front-top">
      <div class="brand">
        <span class="brand-dot"></span>
        <div class="brand-text">
          <span class="brand-name">Mossy Lantern</span>
          <span class="brand-tagline">Climbin' Up the Search Ranks</span>
        </div>
      </div>
      <div class="person">
        <p class="person-name">Jordan Pell</p>
        <p class="person-title">Managing Director</p>
      </div>
    </div>

    <div class="front-band">
      <span class="notch"></span>
      <address class="address">
        Level 12, Harbour Point<br>
        18 Quay Lane, Sydney
      </address>
      <ul class="contacts">
        <li>
          <svg viewBox="0 0 14 14" aria-hidden="true"><rect width="14" height="14" rx="2" fill="#67a61d"/><path d="M4 3.2 5.6 3l.9 2.2-1 .8a6 6 0 0 0 2.6 2.6l.8-1 2.2.9-.2 1.6C9.4 10.6 3.4 6.6 4 3.2Z" fill="#fff"/></svg>
          <span>1300 555 019</span>
        </li>
        <li>
          <svg viewBox="0 0 14 14" aria-hidden="true"><rect width="14" height="14" rx="2" fill="#67a61d"/><rect x="3" y="4" width="8" height="6" fill="none" stroke="#fff" stroke-width="1.2"/><path d="M3 4l4 3.2L11 4" fill="none" stroke="#fff" stroke-width="1.2"/></svg>
          <span>info@mossylantern.com</span>
        </li>
        <li>
          <svg viewBox="0 0 14 14" aria-hidden="true"><rect width="14" height="14" rx="2" fill="#67a61d"/><circle cx="7" cy="7" r="4" fill="none" stroke="#fff" stroke-width="1.1"/><path d="M3 7h8M7 3c-2 2.4-2 5.6 0 8M7 3c2 2.4 2 5.6 0 8" fill="none" stroke="#fff" stroke-width="0.9"/></svg>
          <span>www.mossylantern.com</span>
        </li>
      </ul>
    </div>

    <div class="front-stripe"></div>
  </section>

  <section class="card card-back" aria-label="Business card back">
    <div class="brand">
      <span class="brand-dot"></span>
      <div class="brand-text">
        <span class="brand-name">Mossy Lantern</span>
        <span class="brand-tagline">Climbin' Up the Search Ranks</span>
      </div>
    </div>
  </section>

</main>
</body>
</html>
```